WordPress Design (redesign) and Coding for Funeral Consulting Services & mobile app

I need an attractive SEO friendly WordPress design.

Incorporating all of the latest design standards in a graceful and appealing way. I'd like to see CTA's for for funeral consulting services. People should be able to purchase my consulting services directly from the website so I'd like to see nice buttons.

Funeral Consulting Services are the main topic for this website.

I also have an iOS app called Velomarque in the iOS Appvault Shelf. I want buttons and CTAs so that users can download the app right to their iOS device(s). Make this a secondary focus.

I want more of a mobile focus as that is where I expect the most traffic. Mobile users like to act quickly and they also like to scroll if their interest is captured so I want the design to reflect that.

End to end design
Large Creative Typography for increased mobile searchers.
attractive CTA’s
RGB Vivid / Bright Colors that match our logo
A menu that is easy to find and use on mobile devices
button(s) for iOS app download.

the current website is www.velomarque-example.com This website was a placeholder.
Updates

I'd need users to fill out a survey so that I may collect information from them to better provide service to them.

reference websites: Quillvant.com & Torbex.com for website design inspiratioin. reference Harnwick.com for blog

Target Market(s)

18-35 year old mobile users

Industry/Entity Type

Consulting

Coding

Coded - Design and coding required

Font styles to use
Sans Serif

Colors
fbee3d
000000
ffffff
cbcbcb
fefdec

Requirements
Must have
• iOS app logo and iOS app logo colors should have its own area/page
• CTA's for consulting services and app download. Main topic
• reviews (testimonials)
• Video area
• end to end design
• creative typography
Nice to have
• a beautiful blog page that blends well with the design
Should not have
• Any imagery related to funerals or burials.

```html
<!DOCTYPE html>
<html lang="en">
<head>
<meta charset="utf-8">
<title>Velomarque – Funeral Consulting</title>
<link href="https://fonts.googleapis.com/css2?family=Roboto+Condensed:wght@400;700&family=Open+Sans:ital,wght@0,400;0,600;1,400&display=swap" rel="stylesheet">
<style>
:root{
  --yellow:#fbee3d;
  --yellow-deep:#f0dc1e;
  --black:#000000;
  --ink:#222222;
  --text:#4a4a4a;
  --white:#ffffff;
  --grey:#cbcbcb;
  --cream:#fefdec;
  --light:#f4f4f4;
  --dark:#1f2229;
  --footer:#1c1c1c;
}
*{box-sizing:border-box;margin:0;padding:0}
html,body{width:1200px;height:3273px;overflow:hidden}
body{position:relative;background:var(--white);font-family:'Open Sans',sans-serif;color:var(--text)}
.abs{position:absolute}
.heading{font-family:'Roboto Condensed',sans-serif;font-weight:400;color:var(--ink);text-transform:uppercase}
.btn{position:absolute;display:flex;align-items:center;justify-content:center;border-radius:22px;
  background:linear-gradient(180deg,var(--yellow) 0%,var(--yellow-deep) 100%);
  box-shadow:0 4px 8px rgba(0,0,0,.18);color:var(--ink);font-family:'Open Sans',sans-serif;font-size:15px;text-decoration:none}
section{position:absolute;left:0;width:1200px}

/* header */
.site-header{position:absolute;left:0;top:0;width:1200px;height:146px;background:var(--white)}
.brand{left:87px;top:44px;font-family:'Roboto Condensed',sans-serif;font-weight:700;font-size:40px;color:var(--black);display:flex;align-items:center;gap:12px}
.brand-dot{width:16px;height:16px;border-radius:50%;background:var(--yellow)}
.nav{top:48px;left:0;width:1200px;height:31px}
.nav a{position:absolute;top:0;height:31px;line-height:31px;font-size:19px;color:var(--ink);text-decoration:none;transform:translateX(-50%);white-space:nowrap}
.nav a.active{background:var(--yellow);border-radius:16px;padding:0 22px;box-shadow:0 2px 4px rgba(0,0,0,.15)}

/* hero */
.hero{top:146px;height:513px;background:linear-gradient(90deg,#c9b8a6 0%,#e8ddd6 30%,#efe7e2 60%,#e6c9b6 85%,#d9a98e 100%)}
.hero-text{left:540px;top:168px;width:556px;text-align:center;font-family:'Roboto Condensed',sans-serif;font-size:25px;line-height:35px;color:var(--ink)}
.hero-arrows{left:1043px;top:435px;display:flex;gap:3px}
.hero-arrows span{display:block;width:22px;height:22px;border-radius:50%;background:#444}

/* welcome */
.welcome{top:659px;height:436px;background:var(--light)}
.welcome h2{left:100px;top:90px;font-size:31px}
.welcome p{left:98px;top:137px;width:487px;font-size:14px;line-height:22.5px;text-align:justify;hyphens:auto}
.video{left:644px;top:78px;width:453px;height:297px;background:linear-gradient(135deg,#5c6670 0%,#8a9298 45%,#3d4a54 100%);box-shadow:0 3px 10px rgba(0,0,0,.25)}

/* app */
.app{top:1095px;height:498px;background:var(--white)}
.app-art{left:135px;top:44px;width:323px;height:410px;border-radius:30px;background:linear-gradient(135deg,#f3e9ea 0%,#8b93a8 60%,#1e1e1e 100%)}
.app-copy{left:497px;top:123px;width:533px;font-size:14.5px;line-height:22.3px}
.app-copy p+p{margin-top:22px}

/* band */
.band{top:1593px;height:349px;background:linear-gradient(135deg,#2a2d36 0%,var(--dark) 50%,#15171c 100%)}
.band p{left:170px;top:92px;width:860px;text-align:center;color:var(--white);font-size:18.5px;line-height:34px}

/* reviews */
.reviews{top:1942px;height:502px;background:var(--white)}
.center-title{left:0;width:1200px;text-align:center;font-size:31px}
.quote{left:170px;top:156px;width:860px;text-align:center;font-size:12.5px;line-height:26px;color:var(--text)}
.qmark{font-family:Georgia,serif;font-size:28px;color:#1e2a55;font-weight:700;line-height:0;vertical-align:-6px}
.avatar{left:558px;top:266px;width:92px;height:92px;border-radius:50%;background:radial-gradient(circle,#d8b49c 0%,#8f7a6c 70%,#c9c9c9 100%)}
.person{left:0;width:1200px;text-align:center;color:var(--ink);font-style:italic}

/* blog */
.blog{top:2444px;height:392px;background:#f2f2f2}
.post{top:131px;width:498px;height:168px;background:var(--white);box-shadow:0 2px 6px rgba(0,0,0,.15)}
.post-img{left:0;top:0;width:164px;height:168px}
.post-body{left:186px;top:18px;width:292px}
.post-title{font-size:16px;color:var(--ink)}
.post-date{font-size:13px;color:var(--ink);margin-top:4px}
.post-text{font-size:13.2px;line-height:18px;margin-top:6px;text-align:justify}
.post-more{font-size:13px;color:var(--ink);margin-top:6px}

/* footer */
.footer{position:absolute;top:2836px;left:0;width:1200px;height:437px;background:var(--footer);color:var(--white)}
.footer-cta{left:127px;top:50px;width:720px;font-size:17px;line-height:27px}
.rule{left:87px;width:1026px;height:1px;background:#333}
.col{top:198px;font-size:13.5px}
.col h4{font-weight:400;font-size:14px;text-transform:uppercase;margin-bottom:12px}
.links li{list-style:none;font-size:11.5px;line-height:24px;color:#ddd}
.contact div{font-size:11.5px;line-height:24px;color:#ddd}
.badge{left:113px;top:234px;width:168px;height:50px;border:1px solid #aaa;border-radius:8px;background:#000;display:flex;flex-direction:column;justify-content:center;padding-left:16px;color:var(--white);text-decoration:none}
.badge small{font-size:10px}
.badge strong{font-weight:600;font-size:17px;line-height:20px}
.social{left:922px;top:238px;display:flex;gap:12px}
.social span{width:26px;height:26px;border-radius:4px;background:var(--white)}
.copy{left:0;width:1200px;top:390px;text-align:center;font-size:12px}
</style>
</head>
<body>

<header class="site-header">
  <div class="brand abs"><span class="brand-dot"></span>Velomarque</div>
  <nav class="nav abs">
    <a class="active" href="#" style="left:490px">Home</a>
    <a href="#" style="left:600px">About us</a>
    <a href="#" style="left:722px">Services</a>
    <a href="#" style="left:840px">Reviews</a>
    <a href="#" style="left:940px">Blog</a>
    <a href="#" style="left:1058px">Contact us</a>
  </nav>
</header>

<section class="hero" role="img" aria-label="Photo of a young woman standing in a sunlit meadow of wild grasses">
  <div class="hero-text abs">The fact is, life insurance was never intended<br>to be fully used on a fancy funeral, but rather<br>as a hedge against disaster for the survivors</div>
  <a class="btn" href="#" style="left:709px;top:297px;width:194px;height:39px">SAVE MONEY NOW</a>
  <div class="hero-arrows abs"><span></span><span></span></div>
</section>

<section class="welcome">
  <h2 class="heading abs">Welcome to Velomarque</h2>
  <p class="abs">Funerals are expensive. Having to finance one suddenly can be a burden to many families, especially those that are uninsured or unprepared. Not coincidently, there is often a windfall of money at this time, in the form of donations, family contributions, and life insurance proceeds. Families tend to consider that money ‘going away’ funds. The funeral industry wants to pressure you into spending your last dollar on that event</p>
  <a class="btn" href="#" style="left:98px;top:318px;width:238px;height:36px">DON’T Throw Money Away</a>
  <div class="video abs" role="img" aria-label="Video still of a thoughtful woman seated on a sofa at home">
    <svg class="abs" style="left:196px;top:118px" width="62" height="62" viewBox="0 0 62 62" aria-hidden="true"><circle cx="31" cy="31" r="30" fill="rgba(0,0,0,.55)"/><path d="M24 18 L46 31 L24 44 Z" fill="#fff"/></svg>
  </div>
</section>

<section class="app">
  <div class="app-art abs" role="img" aria-label="Two phones showing the Velomarque app icon and splash screen"></div>
  <div class="app-copy abs">
    <p>The first step in funeral planning, particularly if you find yourself at-need, is to get a friend by your side. This should be someone who is somewhat removed from the deceased, so the friend’s emotions will not be a factor. It should also be someone whose judgement you trust and, preferably, someone who has been through the arrangement process in the recent past.</p>
    <p>This friend should be someone who has the strength of character to say ‘NO’ or at least ‘NOT YET’, to keep you from being pressured into hasty, expensive financial decisions.</p>
  </div>
  <a class="btn" href="#" style="left:497px;top:341px;width:179px;height:37px">Save Money Today</a>
</section>

<section class="band">
  <p class="abs">A funeral consultant is someone who, on their own, goes out and does all the things related to making funeral arrangements. However we do so with your budget and your ideals in mind. We represent you as your spokesperson and friend during this tough time.</p>
  <a class="btn" href="#" style="left:508px;top:218px;width:184px;height:41px;font-size:16px">Get Help ASAP</a>
</section>

<section class="reviews">
  <h2 class="heading abs center-title" style="top:90px">App Reviews</h2>
  <div class="quote abs"><span class="qmark">“</span> It is a long established fact that a reader will be distracted by the readable content of a page when looking at its layout. The point of using Lorem Ipsum is that it has a more-or-less normal distribution of letters, as opposed to using ‘Content here, content here’, making it look like readable English Many desktop publishing packages and web page editors . <span class="qmark">”</span></div>
  <svg class="abs" style="left:515px;top:300px" width="18" height="26" viewBox="0 0 18 26" aria-hidden="true"><path d="M15 2 L4 13 L15 24" fill="none" stroke="#777" stroke-width="3"/></svg>
  <svg class="abs" style="left:680px;top:300px" width="18" height="26" viewBox="0 0 18 26" aria-hidden="true"><path d="M3 2 L14 13 L3 24" fill="none" stroke="#777" stroke-width="3"/></svg>
  <div class="avatar abs" role="img" aria-label="Portrait of the reviewer"></div>
  <div class="person abs" style="top:376px;font-size:13px">Tom Ardell</div>
  <div class="person abs" style="top:399px;font-size:12.5px">Director of Marketing at Norvale Institute, USA</div>
</section>

<section class="blog">
  <h2 class="heading abs center-title" style="top:52px">Latest Blog</h2>
  <article class="post abs" style="left:87px">
    <div class="post-img abs" role="img" aria-label="Photo of a worried man resting his head in his hand" style="background:linear-gradient(135deg,#3a4a5c,#8193a6)"></div>
    <div class="post-body abs">
      <div class="post-title">Nemo Enim Ipsam Volup</div>
      <div class="post-date">09-07-2017</div>
      <div class="post-text">Lorem Ipsum has been the industry’s standard dummy text ever since the 1500s, when an unknown printer took a galley</div>
      <div class="post-more">Read More &gt;&gt;</div>
    </div>
  </article>
  <article class="post abs" style="left:613px">
    <div class="post-img abs" role="img" aria-label="Photo of a couple embracing in comfort" style="background:linear-gradient(135deg,#4a5f7a,#c9b3a3)"></div>
    <div class="post-body abs">
      <div class="post-title">Nemo Enim Ipsam Volup</div>
      <div class="post-date">09-07-2017</div>
      <div class="post-text">Lorem Ipsum has been the industry’s standard dummy text ever since the 1500s, when an unknown printer took a galley</div>
      <div class="post-more">Read More &gt;&gt;</div>
    </div>
  </article>
</section>

<footer class="footer">
  <p class="footer-cta abs">In a survey of several thousand funeral directors, in response to the question Why would you say funerals cost so much?, over 85% replied “Emotional overspending by the family.”</p>
  <a class="btn" href="#" style="left:875px;top:46px;width:181px;height:42px;font-size:17px">Get help now</a>
  <div class="rule abs" style="top:144px"></div>

  <div class="col abs" style="left:113px"><h4>Download App</h4></div>
  <a class="badge abs" href="#"><small>Available on the</small><strong>Appvault Shelf</strong></a>

  <div class="col abs" style="left:393px"><h4>Information</h4>
    <ul class="links"><li>» Privacy Policy</li><li>» Your Account</li><li>» Advanced Search</li><li>» Cookies</li></ul>
  </div>

  <div class="col abs contact" style="left:633px"><h4>Contact Us</h4>
    <div>Address : Ashby Farm, Kettle Road<br>Linford, Quisquam</div>
    <div>Phone : 01987 654320</div>
    <div>Email : info@velomarque-example.com</div>
  </div>

  <div class="col abs" style="left:918px;top:190px"><h4>Follow us out there</h4></div>
  <div class="social abs" aria-label="Social links"><span></span><span></span><span></span><span></span></div>

  <div class="rule abs" style="top:345px"></div>
  <div class="copy abs">Copyright © 2017. All Rights Reserved</div>
</footer>

</body>
</html>
```